Business Cards Design for the electrical wholesaler: clean bold dynamic :)

We need a business card design that would follow our latest brand guidelines. As an electrical wholesaler we want to bring a fresh look and feel into the industry. The design should be clean bold and dynamic. It should come alive with the renewed energy of our green colour. Our grey colour should keep things balanced and complement the notion of maturity and responsibility. We employ Lato as a corporate font however are not bound by this font and we’re open to interpretation here.

Target Market(s)

Electrical contractors

Industry/Entity Type

Business

Contact Information for Business Card

Logo
Name & Surname: Halyna Dorosh
Job Title: Director of Marketing
Email: halya.dorosh@quillmail.example
Cell phone: XXX.XXX.XXXX
Address: 20517 - 87 Ave. Edmonton, AB, Canada. T6K 4N8
Business Phone: 780.555.0184
Website: www.brovix.example

Font styles to use
Other font styles liked:
• Lato

Requirements
Must have
• Logo & website
Nice to have
• Brand elements - some of them you may find in the attached Brand Guidelines (e.g. three lines on the background signifying "W")

```html
<!DOCTYPE html>
<html lang="en">
<head>
<meta charset="utf-8">
<title>Brovix Business Card</title>
<link rel="stylesheet" href="https://fonts.googleapis.com/css2?family=Exo+2:wght@600&family=Roboto:wght@400;500&display=swap">
<style>
  :root {
    --backdrop: #bcbcbc;
    --green-light: #86bd25;
    --green-dark: #5ea82c;
    --grey-light: #4a4d51;
    --grey-dark: #3a3d41;
    --logo-grey: #4a4d52;
    --text-light: #e6e7e8;
    --accent: #7dc11f;
  }
  * { margin: 0; padding: 0; box-sizing: border-box; }
  html, body {
    width: 1200px; height: 576px; overflow: hidden;
    background: var(--backdrop);
  }
  .canvas { position: relative; width: 1200px; height: 576px; }

  .card {
    position: absolute;
    border-radius: 11px;
    overflow: hidden;
  }
  .card-front {
    left: 82px; top: 139px; width: 484px; height: 293px;
    background: linear-gradient(160deg, var(--green-light) 0%, var(--green-dark) 100%);
  }
  .card-back {
    left: 602px; top: 138px; width: 480px; height: 290px;
    background: linear-gradient(170deg, var(--grey-light) 0%, var(--grey-dark) 100%);
    color: var(--text-light);
    font-family: "Roboto", Arial, sans-serif;
    text-align: center;
  }

  .brand {
    position: absolute; left: 0; right: 0; top: 122px;
    display: flex; align-items: center; justify-content: center; gap: 10px;
  }
  .brand-dot {
    width: 30px; height: 30px; border-radius: 50%;
    background: var(--logo-grey);
  }
  .brand-name {
    font-family: "Roboto", Arial, sans-serif;
    font-weight: 500; font-size: 44px; line-height: 1;
    color: var(--logo-grey);
  }

  .holder-name {
    position: absolute; left: 0; right: 0; top: 80px;
    font-family: "Exo 2", Arial, sans-serif; font-weight: 600;
    font-size: 21px; line-height: 24px; color: var(--accent);
  }
  .holder-title {
    position: absolute; left: 0; right: 0; top: 104px;
    font-size: 12.5px; line-height: 16px;
  }
  .contact-icons {
    position: absolute; left: 0; right: 0; top: 149px;
    display: flex; justify-content: center; gap: 2px;
  }
  .contact-icons svg { width: 14px; height: 14px; }
  .contact-line {
    position: absolute; left: 0; right: 0;
    font-size: 13px; line-height: 16px;
  }
  .contact-phone { top: 168px; }
  .contact-web { top: 185px; }
  .divider {
    position: absolute; left: 28px; right: 28px; top: 250px; height: 1px;
    background: linear-gradient(90deg, transparent, var(--accent) 20%, var(--accent) 80%, transparent);
  }
  .address {
    position: absolute; left: 0; right: 0; top: 258px;
    font-size: 13px; line-height: 16px;
  }
</style>
</head>
<body>
<div class="canvas">
  <section class="card card-front">
    <div class="brand">
      <span class="brand-dot"></span>
      <span class="brand-name">brovix</span>
    </div>
  </section>

  <section class="card card-back">
    <div class="holder-name">Halyna Dorosh</div>
    <div class="holder-title">Director of Marketing</div>

    <div class="contact-icons">
      <svg viewBox="0 0 14 14" aria-label="Phone">
        <circle cx="7" cy="7" r="6.2" fill="none" stroke="var(--accent)" stroke-width="1.2"/>
        <path d="M4.6 4.2 L5.8 4 L6.3 5.4 L5.6 6 Q6.2 7.4 7.8 8.2 L8.4 7.6 L9.8 8 L9.7 9.3 Q6.8 9.6 4.6 4.2Z" fill="var(--accent)"/>
      </svg>
      <svg viewBox="0 0 14 14" aria-label="Email">
        <circle cx="7" cy="7" r="6.2" fill="none" stroke="var(--accent)" stroke-width="1.2"/>
        <rect x="4" y="4.8" width="6" height="4.4" fill="var(--accent)"/>
        <path d="M4 4.9 L7 7.2 L10 4.9" fill="none" stroke="var(--grey-dark)" stroke-width="0.7"/>
      </svg>
      <svg viewBox="0 0 14 14" aria-label="Website">
        <circle cx="7" cy="7" r="6.2" fill="none" stroke="var(--accent)" stroke-width="1.2"/>
        <circle cx="7" cy="7" r="3.4" fill="none" stroke="var(--accent)" stroke-width="0.8"/>
        <ellipse cx="7" cy="7" rx="1.4" ry="3.4" fill="none" stroke="var(--accent)" stroke-width="0.7"/>
        <line x1="3.6" y1="7" x2="10.4" y2="7" stroke="var(--accent)" stroke-width="0.7"/>
      </svg>
    </div>

    <div class="contact-line contact-phone">+1 780-555-0184</div>
    <div class="contact-line contact-web">halya.dorosh@quillmail.example | www.brovix.example</div>

    <div class="divider"></div>
    <div class="address">20517 - 87 Ave. Edmonton, AB, Canada T6K 4N8</div>
  </section>
</div>
</body>
</html>
```